Business Card Design

New business card design

Target Market(s)

Residential & Commercial Property Managers

Industry/Entity Type

Plumbing Services

Contact Information for Business Card

Name - Rowan Keddle, title - Director, Phone Number - 0431 286 517, email - rowan@tbk-plumbing.com.au, Company ABN - 73 215 904 386,

Font styles to use
Sans Serif

Colors
0054AA
0677BA
7BADD7
CADEEF
E8F1F8

```html
<!DOCTYPE html>
<html lang="en">
<head>
<meta charset="utf-8">
<title>TBK Plumbing Services — Business Card</title>
<link rel="stylesheet" href="https://fonts.googleapis.com/css2?family=Arimo:wght@400;700&display=swap">
<style>
  :root {
    --backdrop: #3d3d3d;
    --card-white: #ffffff;
    --card-dark: #1e232a;
    --brand-blue: #00aced;
    --rule-blue: #14a3e0;
    --ink: #1e232a;
    --tagline-grey: #6e6e6e;
    --text-light: #ffffff;
    --text-muted: #cfd5db;
  }
  * { box-sizing: border-box; margin: 0; padding: 0; }
  html, body { width: 1200px; height: 803px; overflow: hidden; }
  body {
    background: var(--backdrop);
    font-family: "Arimo", Arial, sans-serif;
    position: relative;
  }
  .card {
    position: absolute;
    top: 253px;
    width: 520px;
    height: 297px;
    border-radius: 22px;
    overflow: hidden;
  }
  .card--front { left: 50px; background: var(--card-white); }
  .card--back  { left: 630px; background: var(--brand-blue); }

  .brand {
    position: absolute;
    left: 0; right: 0;
    text-align: center;
  }
  .brand__name {
    display: inline-flex;
    align-items: center;
    gap: 10px;
    font-size: 76px;
    font-weight: 400;
    letter-spacing: 2px;
    line-height: 1;
    color: var(--ink);
  }
  .brand__dot {
    width: 16px; height: 16px;
    border-radius: 50%;
    background: var(--brand-blue);
  }
  .card--back .brand__dot { background: var(--card-white); }
  .brand__tagline {
    margin-top: 10px;
    font-size: 13px;
    letter-spacing: 11px;
    color: var(--tagline-grey);
  }
  .card--front .brand { top: 34px; }
  .card--back .brand { top: 88px; }
  .card--back .brand__tagline { color: #2c4e66; }

  .card__rule {
    position: absolute;
    left: 0; right: 0;
    top: 168px;
    height: 5px;
    background: var(--rule-blue);
  }
  .card__panel {
    position: absolute;
    left: 0; right: 0;
    top: 173px; bottom: 0;
    background: var(--card-dark);
    display: flex;
    align-items: center;
    justify-content: center;
    gap: 18px;
    color: var(--text-light);
  }
  .person { text-align: right; }
  .person__name { font-size: 24px; font-weight: 700; }
  .person__title { font-size: 14px; color: var(--text-muted); margin-top: 4px; }
  .panel__divider {
    width: 1px; height: 64px;
    background: var(--text-muted);
  }
  .contact { list-style: none; font-size: 14px; line-height: 1.55; }
  .contact li { display: flex; align-items: center; gap: 7px; }
  .contact svg { width: 12px; height: 12px; fill: var(--text-light); }
</style>
</head>
<body>
  <section class="card card--front" aria-label="Business card front">
    <div class="brand">
      <div class="brand__name">tbk<span class="brand__dot"></span></div>
      <div class="brand__tagline">plumbing services</div>
    </div>
    <div class="card__rule"></div>
    <div class="card__panel">
      <div class="person">
        <div class="person__name">Rowan Keddle</div>
        <div class="person__title">Director</div>
      </div>
      <div class="panel__divider"></div>
      <ul class="contact">
        <li>ABN - 73 215 904 386</li>
        <li>
          <svg viewBox="0 0 24 24" aria-hidden="true"><path d="M6.6 10.8a15.1 15.1 0 0 0 6.6 6.6l2.2-2.2a1 1 0 0 1 1-.25 11.4 11.4 0 0 0 3.6.57 1 1 0 0 1 1 1V20a1 1 0 0 1-1 1A17 17 0 0 1 3 4a1 1 0 0 1 1-1h3.5a1 1 0 0 1 1 1c0 1.25.2 2.45.57 3.57a1 1 0 0 1-.25 1z"/></svg>
          0431 286 517
        </li>
        <li>
          <svg viewBox="0 0 24 24" aria-hidden="true"><path d="M2 5h20v14H2z M2 5l10 8 10-8" stroke="#1e232a" stroke-width="1.5"/></svg>
          rowan@tbk-plumbing.com.au
        </li>
      </ul>
    </div>
  </section>

  <section class="card card--back" aria-label="Business card back">
    <div class="brand">
      <div class="brand__name">tbk<span class="brand__dot"></span></div>
      <div class="brand__tagline">plumbing services</div>
    </div>
  </section>
</body>
</html>
```